Retail Jewelry Business Card Design Project

We are in need of a new business card design for a retail jewelry store. This store is in the business of fine jewelry including but not specific to bridal jewelry, diamonds, designer jewelry and watches.

This store has been in business for 20 years but continues to strive for a modern professional appeal. The main colors use for this business are a royal blue, white and silver.

Target Market(s)

Target market is ages 18-50

Industry/Entity Type

Jewelry

Requirements
Must have
• Sales Person Name
Sales Person Email Address

Store Address
Store Phone
Website

Standard business card size. No odd shapes or sizes.
Nice to have
• Overall modern feel for card.

We have thought that a design with a nice feature of the logo on the back of the card would be nice but open to ideas.
Should not have
• No specific images of jewelry should be used.

```html
<!DOCTYPE html>
<html lang="en">
<head>
<meta charset="utf-8">
<title>Marlowe Hayes Fine Jewelry – Business Cards</title>
<link rel="stylesheet" href="https://fonts.googleapis.com/css2?family=Tinos:wght@400;700&family=Courgette&display=swap">
<style>
  :root {
    --royal: #2e3192;
    --white: #ffffff;
    --silver: #c9cbd1;
    --ink: #4a4a4a;
    --stage: #eceef2;
  }
  * { box-sizing: border-box; margin: 0; padding: 0; }
  html, body { width: 1200px; height: 980px; overflow: hidden; }
  body { background: var(--stage); position: relative; font-family: "Tinos", serif; }

  .card {
    position: absolute;
    width: 700px;
    height: 400px;
    border-radius: 36px;
    box-shadow: 0 14px 30px rgba(40, 44, 70, 0.18);
    overflow: hidden;
  }

  .brand {
    position: absolute;
    left: 0;
    right: 0;
    text-align: center;
    font-family: "Tinos", serif;
    font-weight: 400;
    line-height: 1.1;
  }

  /* Back of card */
  .card--back { left: 440px; top: 60px; background: var(--royal); color: var(--white); }
  .card--back .brand { top: 150px; font-size: 46px; color: var(--white); }
  .card--back .web {
    position: absolute; left: 0; right: 0; bottom: 70px;
    text-align: center; font-size: 20px; letter-spacing: 4px; color: var(--white);
  }

  /* Front of card */
  .card--front { left: 60px; top: 520px; background: var(--white); color: var(--royal); }
  .card--front .brand { top: 62px; font-size: 42px; color: var(--royal); }
  .card--front .person {
    position: absolute; left: 0; right: 0; top: 150px;
    text-align: center; font-family: "Courgette", cursive; font-size: 26px; color: var(--royal);
  }
  .card--front .divider {
    position: absolute; left: 60px; right: 60px; top: 214px; height: 2px;
    background: linear-gradient(90deg, transparent, var(--silver) 15%, var(--silver) 85%, transparent);
  }

  .contact { position: absolute; left: 0; right: 0; top: 244px; font-size: 19px; color: var(--ink); }
  .contact__row { display: flex; justify-content: center; align-items: center; gap: 26px; margin-bottom: 16px; }
  .contact__item { display: flex; align-items: center; gap: 8px; white-space: nowrap; }
  .contact__icon { width: 18px; height: 18px; flex: none; }
  .contact__address { text-align: center; }
</style>
</head>
<body>

  <section class="card card--back" aria-label="Card back">
    <div class="brand">Marlowe Hayes Fine Jewelry</div>
    <div class="web">www.marlowehayesjewelry.com</div>
  </section>

  <section class="card card--front" aria-label="Card front">
    <div class="brand">Marlowe Hayes Fine Jewelry</div>
    <div class="person">Marlowe Hayes Whitford</div>
    <div class="divider"></div>

    <div class="contact">
      <div class="contact__row">
        <span class="contact__item">
          <svg class="contact__icon" viewBox="0 0 20 20" aria-hidden="true">
            <circle cx="10" cy="10" r="9" fill="var(--royal)"/>
            <path d="M7 5.5c.6-.4 1.2-.3 1.5.3l.8 1.6c.2.5 0 .9-.4 1.2l-.6.4c.5 1.2 1.3 2 2.5 2.5l.4-.6c.3-.4.7-.6 1.2-.4l1.6.8c.6.3.7.9.3 1.5-.6.9-1.5 1.3-2.5 1-2.6-.8-4.4-2.6-5.2-5.2-.3-1 .1-1.9 1-2.5z" fill="var(--white)"/>
          </svg>
          555-201-4870
        </span>
      </div>
      <div class="contact__row">
        <span class="contact__item">
          <svg class="contact__icon" viewBox="0 0 20 20" aria-hidden="true">
            <rect x="2" y="4" width="16" height="12" rx="2" fill="var(--royal)"/>
            <path d="M3 5.5l7 5 7-5" stroke="var(--white)" stroke-width="1.5" fill="none"/>
          </svg>
          marlowe@marlowehayesjewelry.com
        </span>
        <span class="contact__item">
          <svg class="contact__icon" viewBox="0 0 20 20" aria-hidden="true">
            <circle cx="10" cy="10" r="8.5" fill="var(--royal)"/>
            <g stroke="var(--white)" stroke-width="1.1" fill="none">
              <ellipse cx="10" cy="10" rx="3.6" ry="8.5"/>
              <line x1="1.5" y1="10" x2="18.5" y2="10"/>
              <path d="M3 6h14M3 14h14"/>
            </g>
          </svg>
          www.marlowehayesjewelry.com
        </span>
      </div>
      <div class="contact__address">2280 Calloway Street, Bayport, FL 32999</div>
    </div>
  </section>

</body>
</html>
```